Wireless Internet Service Provider website design

We need a Internet Service Provider website that show the packages that we offer as well as the functionality where customers have the option of clicking on the various packages and be linked to a page where they can sign up for our services.
We need about 10-15 pages.
A. Integrated online store.
B. Live chat.
C. Social media page
My old website. Brightlinkradio.nyc

Example: http://plumcrestnet.com/services/residential/ Added Tuesday, June 7, 2016

Target Market(s)

Residential and small businesses

Industry/Entity Type

Internet

Coding

Coded - Design and coding required

Number of Pages Required

5+ page

Font styles to use
Serif
Sans Serif
Script

Colors
3176b5
85cae6
ffffff

Requirements
Must have
• Online store and live chat, drop down details on pricing from current website
Nice to have
• great design, functional website,

```html
<!DOCTYPE html>
<html lang="en">
<head>
<meta charset="utf-8">
<title>Brightlink Radio – Residential and Business Internet</title>
<link href="https://fonts.googleapis.com/css2?family=Raleway:wght@500;600;700&family=Open+Sans:ital,wght@0,400;0,600;0,700;1,400&display=swap" rel="stylesheet">
<style>
:root{
  --brand:#1a7fb3;
  --brand-dark:#0b6793;
  --brand-deep:#0a5a82;
  --sky:#85cae6;
  --ink:#333;
  --text:#555;
  --muted:#777;
  --rule:#e3e3e3;
  --panel:#eeeeee;
  --footer:#242424;
  --footer-bar:#1a1a1a;
  --white:#fff;
}
*{box-sizing:border-box;margin:0;padding:0}
html,body{width:1200px;height:2535px;overflow:hidden}
body{position:relative;background:var(--white);font-family:"Open Sans",Arial,sans-serif;color:var(--text)}
.abs{position:absolute}

/* header */
.top-line{left:0;top:0;width:1200px;height:4px;background:var(--brand-dark)}
.site-header{left:0;top:4px;width:1200px;height:145px;background:var(--white)}
.brand{left:98px;top:64px;display:flex;align-items:center;gap:10px;font-family:"Open Sans",sans-serif;font-weight:700;font-size:31px;color:#4a4a4a;letter-spacing:-.5px}
.brand-dot{width:22px;height:22px;border-radius:50%;background:var(--brand)}
.utility{left:696px;top:44px;display:flex;align-items:center;gap:14px;font-size:14px;color:#333}
.utility .phone{display:flex;align-items:center;gap:7px;font-size:19px;color:#333;margin-right:14px}
.utility .sep{color:#999}
.main-nav{left:463px;top:96px;display:flex;gap:0;font-family:"Raleway",sans-serif;font-weight:700;font-size:12.5px;color:#333}
.main-nav a{color:inherit;text-decoration:none;padding:0 0 10px;margin-right:40px}
.main-nav a.active{color:var(--brand);border-bottom:2px solid var(--brand)}

/* hero */
.hero{left:0;top:149px;width:1200px;height:513px;background:radial-gradient(ellipse at 55% 95%,#1e6f96 0%,#11496b 35%,#0b2c44 65%,#0a1a28 100%)}
.hero-rule{left:290px;top:372px;width:620px;height:3px;background:rgba(255,255,255,.55)}
.hero-title{left:0;top:378px;width:1200px;text-align:center;font-family:"Raleway",sans-serif;font-weight:700;font-size:37px;color:var(--white)}
.hero-cta{left:529px;top:443px;width:142px;height:42px;background:var(--brand-dark);color:var(--white);font-family:"Raleway",sans-serif;font-weight:700;font-size:11.5px;display:flex;align-items:center;justify-content:center;letter-spacing:.3px}
.hero-arrow{top:380px}

/* section headings */
.sec-title{left:0;width:1200px;text-align:center;font-family:"Raleway",sans-serif;font-weight:700;font-size:35px;color:#444}
.sec-mark{left:455px;width:290px;height:14px}

/* welcome */
.intro{left:169px;top:790px;width:862px;text-align:center;font-size:12.5px;line-height:27px;color:var(--text)}
.feature{width:320px;text-align:center}
.feature-icon{width:92px;height:92px;margin:0 auto;background:var(--brand);border-radius:6px;opacity:.92}
.feature h3{margin-top:30px;font-family:"Raleway",sans-serif;font-weight:700;font-size:14.5px;color:#333;letter-spacing:.2px}
.feature p{margin-top:14px;font-size:12.5px;line-height:22px;color:var(--muted)}

/* plans */
.plans-bg{left:0;top:1146px;width:1200px;height:558px;background:var(--panel);border-top:1px solid #ddd}
.plan{background:var(--white);border:1px solid #cfe3ee;box-shadow:0 2px 4px rgba(0,0,0,.08)}
.plan-head{height:95px;background:linear-gradient(#1a93c7,#0c77aa);color:var(--white);text-align:center;padding-top:26px;border-top:3px solid #0d6c9a}
.plan-head h4{font-weight:600;font-size:21px}
.plan-head .price{margin-top:2px;font-weight:600;font-size:16px}
.plan-head .price small{font-size:10px;font-weight:400}
.plan ul{list-style:none;margin:8px 18px 0}
.plan li{display:flex;align-items:center;gap:10px;font-size:12.5px;color:#666;height:34px;border-bottom:1px solid var(--rule)}
.plan-btn{position:absolute;left:26px;right:26px;bottom:-2px;height:42px;background:var(--brand);border-bottom:3px solid var(--brand-deep);color:var(--white);font-weight:700;font-size:17px;display:flex;align-items:center;justify-content:center}
.plan.featured{box-shadow:0 6px 14px rgba(0,0,0,.22);z-index:2}
.plan.featured .plan-head{height:88px;padding-top:20px}
.ribbon{right:-3px;top:-3px}

/* news + testimonials */
.col-title{font-family:"Raleway",sans-serif;font-weight:700;font-size:34px;color:#333}
.col-rule{height:14px;width:205px}
.news-thumb{width:145px;height:115px;border:4px solid var(--white);box-shadow:0 0 0 1px #ddd}
.news-body{width:360px}
.news-body h5{font-size:13.5px;font-weight:400;color:#222}
.news-body .date{display:flex;align-items:center;gap:10px;margin-top:12px;font-size:12.5px;color:var(--brand)}
.news-body p{margin-top:8px;font-size:12.5px;line-height:22px;color:#555}
.quote-box{left:669px;top:1851px;width:438px;height:152px;background:#f7f8fa;border:1px solid #ececec;padding:18px 22px 0 40px;font-style:italic;font-size:12px;line-height:23px;color:#999}
.quote-box .q{position:absolute;font-size:30px;color:#aaa;font-style:normal}
.avatar{left:685px;top:2028px;width:68px;height:68px;border-radius:50%;background:linear-gradient(#d8dde2,#a9b3bd);border:3px solid var(--white);box-shadow:0 0 0 1px #ddd}
.author{left:777px;top:2034px;font-size:16px;color:#333}
.author b{font-weight:400;color:var(--brand)}
.pager{top:2070px;width:22px;height:22px;border:1px solid #ddd;border-radius:3px;display:flex;align-items:center;justify-content:center}
.chat-tab{left:1163px;top:2028px;width:37px;height:118px;background:#6cbfc9;border-radius:6px 0 0 6px;color:var(--white);font-size:11px;font-weight:700}
.chat-tab span{position:absolute;left:8px;top:80px;transform:rotate(-90deg);transform-origin:left top;white-space:nowrap;letter-spacing:.5px}

/* newsletter */
.newsletter{left:0;top:2157px;width:1200px;height:67px;background:var(--brand-dark)}
.nl-icon{left:93px;top:2167px;width:46px;height:46px;border:2px solid var(--white);border-radius:50%;display:flex;align-items:center;justify-content:center}
.nl-title{left:189px;top:2169px;font-family:"Raleway",sans-serif;font-weight:500;font-size:29px;color:var(--white)}
.nl-input{left:520px;top:2169px;width:438px;height:43px;background:var(--white);font-size:14px;color:#888;padding:12px 12px}
.nl-btn{left:982px;top:2169px;width:132px;height:43px;background:#2a9fcf;color:var(--white);font-size:15.5px;display:flex;align-items:center;justify-content:center;box-shadow:inset 0 -3px 0 #1a7fa8}

/* footer */
.footer{left:0;top:2224px;width:1200px;height:264px;background:var(--footer)}
.footer-brand{left:95px;top:2290px;display:flex;align-items:center;gap:10px;font-weight:700;font-size:31px;color:var(--white);letter-spacing:-.5px}
.footer-brand .brand-dot{background:var(--white)}
.footer-about{left:95px;top:2345px;width:280px;font-size:12.5px;line-height:24.5px;color:#eee;text-align:justify}
.f-head{font-family:"Raleway",sans-serif;font-size:20px;color:#eee;padding-bottom:6px;border-bottom:1px solid #888}
.links{list-style:none;margin-top:6px}
.links li{font-size:12.5px;color:#ddd;line-height:25px;display:flex;align-items:center;gap:8px}
.map{left:612px;top:2295px;width:241px;height:156px;background:linear-gradient(135deg,#ece6d6,#d9d3c2);border:3px solid #555}
.contact-row{left:887px;display:flex;gap:14px;font-size:13px;color:#eee;line-height:21px}
.contact-row svg{flex:none;margin-top:3px}
.footer-bar{left:0;top:2488px;width:1200px;height:47px;background:var(--footer-bar)}
.copyright{left:95px;top:2503px;font-size:12.5px;color:#ccc}
.social{top:2496px;width:34px;height:34px;border-radius:50%}
</style>
</head>
<body>

<div class="abs top-line"></div>
<header class="abs site-header"></header>
<div class="abs brand"><span class="brand-dot"></span>BrightlinkRadio</div>
<div class="abs utility">
  <span class="phone">
    <svg width="17" height="17" viewBox="0 0 24 24"><path fill="#1a7fb3" d="M6.6 10.8a15.1 15.1 0 0 0 6.6 6.6l2.2-2.2c.3-.3.7-.4 1-.2 1.1.4 2.3.6 3.6.6.6 0 1 .4 1 1V20c0 .6-.4 1-1 1A17 17 0 0 1 3 4c0-.6.4-1 1-1h3.5c.6 0 1 .4 1 1 0 1.3.2 2.5.6 3.6.1.3 0 .7-.2 1z"/></svg>
    (866) 555-0142
  </span>
  <span>Login</span><span class="sep">|</span><span>Register</span><span class="sep">|</span><span>Support</span><span class="sep">|</span><span>Sitemap</span>
</div>
<nav class="abs main-nav">
  <a class="active">HOME</a><a>WHY BRIGHTLINK</a><a>PLANS &amp; PACKAGES</a><a>MY ACCOUNT</a><a>GALLERY</a><a>CONTACTS</a>
</nav>

<section class="abs hero" role="img" aria-label="Hand holding a tablet above a glowing globe with network lines and service icons over a night city"></section>
<div class="abs hero-rule"></div>
<h1 class="abs hero-title">Residential and Businesses access</h1>
<div class="abs hero-cta">CALL TO ACTION</div>
<svg class="abs hero-arrow" style="left:36px" width="16" height="50" viewBox="0 0 16 50"><path d="M14 2 2 25l12 23" fill="none" stroke="#fff" stroke-width="1.5" opacity=".8"/></svg>
<svg class="abs hero-arrow" style="left:1146px" width="16" height="50" viewBox="0 0 16 50"><path d="m2 2 12 23L2 48" fill="none" stroke="#fff" stroke-width="1.5" opacity=".8"/></svg>

<h2 class="abs sec-title" style="top:700px">Welcome to Brightlink Radio</h2>
<svg class="abs sec-mark" style="top:752px" viewBox="0 0 290 14"><path d="M0 7h128M162 7h128" stroke="#1a7fb3" stroke-width="3"/><path d="m135 2 10 10 10-10" fill="none" stroke="#1a7fb3" stroke-width="3"/></svg>
<p class="abs intro">Brightlink Radio is a highly reputable company, which is aiming at providing high quality internet access and phone services to a market that is continually growing. We are dedicated to filling the digital gap that has been created</p>

<div class="abs feature" style="left:100px;top:887px">
  <div class="feature-icon" role="img" aria-label="Building with network connections icon"></div>
  <h3>RESIDENTIAL INTERNET ACCESS</h3>
  <p>Brightlink's VOIP home phone solutions offer you a reliable, portable, low-cost alternative to traditional home phone service using the Brightlink</p>
</div>
<div class="abs feature" style="left:440px;top:887px">
  <div class="feature-icon" role="img" aria-label="Business user at a monitor icon"></div>
  <h3>BUSINESS INTERNET ACCESS</h3>
  <p>Brightlink's VOIP home phone solutions offer you a reliable, portable, low-cost alternative to traditional home phone service using the Brightlink</p>
</div>
<div class="abs feature" style="left:773px;top:887px">
  <div class="feature-icon" role="img" aria-label="Person working at a desk icon"></div>
  <h3>UNLIMITED INTERNET USAGE</h3>
  <p>Brightlink's VOIP home phone solutions offer you a reliable, portable, low-cost alternative to traditional home phone service using the Brightlink</p>
</div>

<div class="abs plans-bg"></div>
<h2 class="abs sec-title" style="top:1190px">Plans &amp; Packages</h2>
<svg class="abs sec-mark" style="top:1242px" viewBox="0 0 290 14"><path d="M0 7h128M162 7h128" stroke="#1a7fb3" stroke-width="3"/><path d="m135 2 10 10 10-10" fill="none" stroke="#1a7fb3" stroke-width="3"/></svg>

<div class="abs plan" style="left:132px;top:1298px;width:224px;height:321px">
  <div class="plan-head"><h4>Brightlink Simple</h4><div class="price">$39.99 <small>mo./1yr</small></div></div>
  <ul>
    <li><svg width="10" height="9" viewBox="0 0 10 9"><path d="m1 4.5 3 3 5-6" fill="none" stroke="#1a7fb3" stroke-width="2"/></svg>Free smart router</li>
    <li><svg width="10" height="9" viewBox="0 0 10 9"><path d="m1 4.5 3 3 5-6" fill="none" stroke="#1a7fb3" stroke-width="2"/></svg>Free internet protection</li>
    <li><svg width="10" height="9" viewBox="0 0 10 9"><path d="m1 4.5 3 3 5-6" fill="none" stroke="#1a7fb3" stroke-width="2"/></svg>Unlimited Speed</li>
    <li><svg width="10" height="9" viewBox="0 0 10 9"><path d="m1 4.5 3 3 5-6" fill="none" stroke="#1a7fb3" stroke-width="2"/></svg>Wi-Fi access</li>
  </ul>
  <div class="plan-btn">Sign up</div>
</div>
<div class="abs plan featured" style="left:355px;top:1281px;width:248px;height:367px">
  <div class="plan-head"><h4>Brightlink Simple</h4><div class="price">$39.99 <small>mo./1yr</small></div></div>
  <svg class="abs ribbon" width="66" height="66" viewBox="0 0 66 66"><path d="M14 0h20l32 32v20z" fill="#85cae6"/><text x="41" y="25" transform="rotate(45 41 25)" font-family="Open Sans,sans-serif" font-size="8" font-weight="700" fill="#fff" text-anchor="middle">BEST VALUE</text></svg>
  <ul>
    <li><svg width="10" height="9" viewBox="0 0 10 9"><path d="m1 4.5 3 3 5-6" fill="none" stroke="#1a7fb3" stroke-width="2"/></svg>Free smart router</li>
    <li><svg width="10" height="9" viewBox="0 0 10 9"><path d="m1 4.5 3 3 5-6" fill="none" stroke="#1a7fb3" stroke-width="2"/></svg>Free internet protection</li>
    <li><svg width="10" height="9" viewBox="0 0 10 9"><path d="m1 4.5 3 3 5-6" fill="none" stroke="#1a7fb3" stroke-width="2"/></svg>Unlimited Speed</li>
    <li><svg width="10" height="9" viewBox="0 0 10 9"><path d="m1 4.5 3 3 5-6" fill="none" stroke="#1a7fb3" stroke-width="2"/></svg>Wi-Fi access</li>
  </ul>
  <div class="plan-btn" style="height:46px;font-size:19px">Sign up</div>
</div>
<div class="abs plan" style="left:603px;top:1298px;width:224px;height:321px">
  <div class="plan-head"><h4>Brightlink Simple</h4><div class="price">$39.99 <small>mo./1yr</small></div></div>
  <ul>
    <li><svg width="10" height="9" viewBox="0 0 10 9"><path d="m1 4.5 3 3 5-6" fill="none" stroke="#1a7fb3" stroke-width="2"/></svg>Free smart router</li>
    <li><svg width="10" height="9" viewBox="0 0 10 9"><path d="m1 4.5 3 3 5-6" fill="none" stroke="#1a7fb3" stroke-width="2"/></svg>Free internet protection</li>
    <li><svg width="10" height="9" viewBox="0 0 10 9"><path d="m1 4.5 3 3 5-6" fill="none" stroke="#1a7fb3" stroke-width="2"/></svg>Unlimited Speed</li>
    <li><svg width="10" height="9" viewBox="0 0 10 9"><path d="m1 4.5 3 3 5-6" fill="none" stroke="#1a7fb3" stroke-width="2"/></svg>Wi-Fi access</li>
  </ul>
  <div class="plan-btn">Sign up</div>
</div>
<div class="abs plan" style="left:826px;top:1298px;width:222px;height:321px">
  <div class="plan-head"><h4>Brightlink Simple</h4><div class="price">$39.99 <small>mo./1yr</small></div></div>
  <ul>
    <li><svg width="10" height="9" viewBox="0 0 10 9"><path d="m1 4.5 3 3 5-6" fill="none" stroke="#1a7fb3" stroke-width="2"/></svg>Free smart router</li>
    <li><svg width="10" height="9" viewBox="0 0 10 9"><path d="m1 4.5 3 3 5-6" fill="none" stroke="#1a7fb3" stroke-width="2"/></svg>Free internet protection</li>
    <li><svg width="10" height="9" viewBox="0 0 10 9"><path d="m1 4.5 3 3 5-6" fill="none" stroke="#1a7fb3" stroke-width="2"/></svg>Unlimited Speed</li>
    <li><svg width="10" height="9" viewBox="0 0 10 9"><path d="m1 4.5 3 3 5-6" fill="none" stroke="#1a7fb3" stroke-width="2"/></svg>Wi-Fi access</li>
  </ul>
  <div class="plan-btn">Sign up</div>
</div>

<h2 class="abs col-title" style="left:98px;top:1768px">Latest news</h2>
<svg class="abs col-rule" style="left:98px;top:1817px" viewBox="0 0 205 14"><path d="M0 4h82M106 4h99" stroke="#1a7fb3" stroke-width="2"/><path d="m86 2 8 8 8-8" fill="none" stroke="#1a7fb3" stroke-width="3"/></svg>

<div class="abs news-thumb" style="left:106px;top:1851px" role="img" aria-label="Couple looking at a laptop together" ><div style="width:100%;height:100%;background:linear-gradient(#c9ccd0,#8e99a4)"></div></div>
<div class="abs news-body" style="left:270px;top:1847px">
  <h5>FAST INTERNET CONNECTIVITY</h5>
  <div class="date"><svg width="14" height="14" viewBox="0 0 14 14"><rect x="1" y="2" width="12" height="11" fill="none" stroke="#1a7fb3" stroke-width="1.5"/><path d="M1 5.5h12M4 0v3M10 0v3" stroke="#1a7fb3" stroke-width="1.5"/></svg>05/03/2016</div>
  <p>When shopping for internet access, people usually look for what is reliable, fast and affordable. This description fits Brightlink Radio LLC the best.</p>
</div>
<div class="abs news-thumb" style="left:106px;top:2000px" role="img" aria-label="Man in a shirt holding a tablet"><div style="width:100%;height:100%;background:linear-gradient(#e4e6e8,#a8b0b8)"></div></div>
<div class="abs news-body" style="left:270px;top:1995px">
  <h5>AFFORDABILITY</h5>
  <div class="date"><svg width="14" height="14" viewBox="0 0 14 14"><rect x="1" y="2" width="12" height="11" fill="none" stroke="#1a7fb3" stroke-width="1.5"/><path d="M1 5.5h12M4 0v3M10 0v3" stroke="#1a7fb3" stroke-width="1.5"/></svg>05/03/2016</div>
  <p>Brightlink offers high speed internet to meet your needs at an affordable price. Finally the internet that you have been waiting for is only a click away.</p>
</div>

<h2 class="abs col-title" style="left:659px;top:1768px">Testimonials</h2>
<svg class="abs col-rule" style="left:662px;top:1817px" viewBox="0 0 205 14"><path d="M0 4h82M106 4h99" stroke="#1a7fb3" stroke-width="2"/><path d="m86 2 8 8 8-8" fill="none" stroke="#1a7fb3" stroke-width="3"/></svg>
<div class="abs quote-box">
  <span class="q" style="left:14px;top:6px">“</span>
  While you are at a café, hotel, park or any other place away from your home, get updated through using the Wi-Fi hotspots, which are available in different places. These hotspots are fast and reliable. All you have to do is use your internet enabled phone view plans
  <span class="q" style="left:400px;top:100px">”</span>
</div>
<div class="abs avatar" role="img" aria-label="Portrait of the customer"></div>
<div class="abs author"><b>Mark Ellison</b> - IT Manager</div>
<div class="abs pager" style="left:788px"><svg width="6" height="9" viewBox="0 0 6 9"><path d="M5 1 1 4.5 5 8" fill="none" stroke="#1a7fb3" stroke-width="1.5"/></svg></div>
<div class="abs pager" style="left:815px"><svg width="6" height="9" viewBox="0 0 6 9"><path d="m1 1 4 3.5L1 8" fill="none" stroke="#1a7fb3" stroke-width="1.5"/></svg></div>
<div class="abs chat-tab"><span>LIVE CHAT</span></div>

<div class="abs newsletter"></div>
<div class="abs nl-icon"><svg width="20" height="14" viewBox="0 0 20 14"><rect width="20" height="14" rx="1" fill="#fff"/><path d="m1 1 9 7 9-7" fill="none" stroke="#0b6793" stroke-width="1.5"/></svg></div>
<div class="abs nl-title">Newsletter Signup</div>
<svg class="abs" style="left:463px;top:2169px" width="16" height="43" viewBox="0 0 16 43"><path d="m2 2 12 19.5L2 41" fill="none" stroke="#85cae6" stroke-width="1.5"/></svg>
<div class="abs nl-input">Enter your email address...</div>
<div class="abs nl-btn">Sign Up</div>

<footer class="abs footer"></footer>
<div class="abs footer-brand"><span class="brand-dot"></span>BrightlinkRadio</div>
<p class="abs footer-about">Brightlink Radio is a highly reputable company, which is aiming at providing high quality internet access and phone services to a market that is continually growing. We are dedicated to filling the digital gap that has been created</p>

<div class="abs" style="left:417px;top:2253px;width:112px">
  <div class="f-head">Quick Links</div>
  <ul class="links">
    <li>›&nbsp;Home</li><li>›&nbsp;Why Brightlink</li><li>›&nbsp;Plans &amp; Packges</li><li>›&nbsp;My account</li><li>›&nbsp;Gallery</li><li>›&nbsp;Contacts</li>
  </ul>
</div>
<div class="abs" style="left:608px;top:2253px;width:136px"><div class="f-head">Contact details</div></div>
<div class="abs map" role="img" aria-label="Street map showing the office location"></div>

<div class="abs contact-row" style="top:2296px">
  <svg width="12" height="16" viewBox="0 0 12 16"><path d="M6 0a6 6 0 0 0-6 6c0 4.5 6 10 6 10s6-5.5 6-10a6 6 0 0 0-6-6zm0 8.5A2.5 2.5 0 1 1 6 3.5a2.5 2.5 0 0 1 0 5z" fill="#fff"/></svg>
  <span>P O Box 410577<br>Brooklyn NY 11201</span>
</div>
<div class="abs contact-row" style="top:2349px">
  <svg width="15" height="15" viewBox="0 0 24 24"><path fill="#fff" d="M6.6 10.8a15.1 15.1 0 0 0 6.6 6.6l2.2-2.2c.3-.3.7-.4 1-.2 1.1.4 2.3.6 3.6.6.6 0 1 .4 1 1V20c0 .6-.4 1-1 1A17 17 0 0 1 3 4c0-.6.4-1 1-1h3.5c.6 0 1 .4 1 1 0 1.3.2 2.5.6 3.6.1.3 0 .7-.2 1z"/></svg>
  <span style="font-size:14.5px">866) 555-0142</span>
</div>
<div class="abs contact-row" style="top:2384px">
  <svg width="16" height="15" viewBox="0 0 16 15"><rect x="0" y="4" width="16" height="11" rx="1" fill="#fff"/><rect x="3" y="0" width="10" height="5" fill="#fff"/><rect x="3" y="7" width="10" height="2" fill="#242424"/></svg>
  <span style="font-size:14.5px">718-555-0199</span>
</div>
<div class="abs contact-row" style="top:2418px">
  <svg width="16" height="12" viewBox="0 0 16 12"><rect width="16" height="12" rx="1" fill="#fff"/><path d="m1 1 7 6 7-6" fill="none" stroke="#242424" stroke-width="1.3"/></svg>
  <span style="font-size:12.5px">support@brightlinkradio.nyc</span>
</div>

<div class="abs footer-bar"></div>
<div class="abs copyright">© brightlinkradio 2016. All right reserved</div>
<span class="abs social" style="left:977px;background:#3b5a98"></span>
<span class="abs social" style="left:1014px;background:#2aa3de"></span>
<span class="abs social" style="left:1051px;background:#1a77b5"></span>
<span class="abs social" style="left:1088px;background:#e88a2a"></span>

</body>
</html>
```